BRAMBLEFORD CONSTRUCTIONS B-Card

I currently have a b-card design but will be removing the image (tree) from the logo and have text only.
I want the card to be classy and strong within the building and construction industry.
I will be using Spot UV on the cards as per the attached examples. I will also send through some sketched ideas that I have in mind.
The color blue is similar to the image (No. 6) attached images

Target Market(s)

middle to maturre aged.
Home Owners / Renovators and Builders

Industry/Entity Type

Construction

Contact Information for Business Card

BRAMBLEFORD CONSTRUCTIONS
Name: Gareth Pennick
Title: Project Manager
Mobile: 0427 351 804
Office: (08) 9316 5172
Address: 47C Corvell Street, Tarrowby WA 6081
Email: info@bramblefordhomes.com.au
PO Box: 3817 Malaga WA 6944

Colors
0592cd
33a6d7
85cae6
1b1b1b

Requirements
Must have
• 1. It must have spot UV on the front of card, maybe back of card too
• 2. I really like the blue on image 6. (or at least a really cool electric blue against the charcoal grey background)
• 3. The font must be slimline and modern. Easy to read
• 4. There must be no black used on the card... Only greys and dark charcoal greys
• 5. Use only the text from the logo "Brambleford Constructions" Not the image of the tree. I am wanting the b-cards to be more masculine.
Nice to have
• 1. I like the design concept on image 6. but happy to see what else you can do with the Spot UV
• 2. Unless you have a really cool idea of the image of the tree (from previous logo) Spot UV somewhere in the design concept thats original and different then I am keen to see what you come up with
• 3. Try changing the color of the logo eg. full white or Blue and white
• 4. Another option is to have the Brambleford Logo on the front of card with the spot UV in the background of text which we specialise in eg, Roofing, Ceiling, Insulation, Gutter Guards, Electrical, Insurance etc and we can add or reduce items as required. Similar to image 12.
Should not have
• Do not include the image of the tree from previous logo. unless you have a really cool idea of Spot UV somewhere in the design concept thats original and different.

```html
<!DOCTYPE html>
<html lang="en">
<head>
<meta charset="utf-8">
<title>Brambleford Constructions Business Card</title>
<link href="https://fonts.googleapis.com/css2?family=Open+Sans:wght@400;600&display=swap" rel="stylesheet">
<style>
  :root {
    --page-bg: #e4e2df;
    --electric-blue: #2ea9e1;
    --charcoal: #232323;
    --charcoal-soft: #2f2f2f;
    --white: #ffffff;
  }
  * { margin: 0; padding: 0; box-sizing: border-box; }
  html, body {
    width: 1200px; height: 1000px; overflow: hidden;
    background: var(--page-bg);
    font-family: "Open Sans", Arial, sans-serif;
  }
  .canvas { position: relative; width: 1200px; height: 1000px; }
  .card {
    position: absolute; left: 265px; width: 666px; height: 397px;
    box-shadow: 0 3px 8px rgba(0,0,0,0.25);
  }
  .card--front { top: 73px; background: var(--electric-blue); color: var(--white); }
  .card--back { top: 532px; background: var(--charcoal); }

  .wordmark { font-weight: 600; text-transform: uppercase; line-height: 1; }
  .wordmark span { display: block; }
  .wordmark__main { letter-spacing: 0.01em; }

  .card--front .wordmark {
    position: absolute; right: 33px; top: 60px; text-align: right; color: var(--white);
  }
  .card--front .wordmark__main { font-size: 43px; }
  .card--front .wordmark__sub { font-size: 17px; letter-spacing: 0.5em; margin-top: 7px; margin-right: -0.5em; }

  .contact { position: absolute; left: 33px; top: 175px; font-size: 16px; line-height: 1.4; }
  .contact__name { font-size: 19px; font-weight: 600; letter-spacing: 0.01em; }
  .contact__title { margin-bottom: 14px; }
  .contact__row { display: flex; align-items: center; gap: 6px; }
  .contact__row svg { width: 16px; height: 16px; fill: var(--white); flex: none; }
  .contact__address { margin-top: 6px; line-height: 1.65; }

  .spot-uv-art {
    position: absolute; left: 140px; top: 18px; width: 386px; height: 362px;
    border-radius: 50%;
    background: radial-gradient(ellipse at center, var(--charcoal-soft) 0%, #2a2a2a 55%, var(--charcoal) 75%);
  }
  .card--back .wordmark {
    position: absolute; left: 0; right: 0; top: 160px; text-align: center; color: var(--electric-blue);
  }
  .card--back .wordmark__main { font-size: 52px; }
  .card--back .wordmark__sub { font-size: 21px; letter-spacing: 0.5em; margin-top: 12px; margin-right: -0.5em; }
</style>
</head>
<body>
<main class="canvas">
  <section class="card card--front">
    <div class="wordmark">
      <span class="wordmark__main">Brambleford</span>
      <span class="wordmark__sub">Constructions</span>
    </div>
    <div class="contact">
      <p class="contact__name">GARETH PENNICK</p>
      <p class="contact__title">Project Manager</p>
      <p class="contact__row">
        <svg viewBox="0 0 16 16" aria-hidden="true"><path d="M4.5 1h7a1 1 0 0 1 1 1v12a1 1 0 0 1-1 1h-7a1 1 0 0 1-1-1V2a1 1 0 0 1 1-1zm.5 2v9h6V3zm3 10a.7.7 0 1 0 0 .01z" fill-rule="evenodd"/></svg>
        0427 351 804
      </p>
      <p class="contact__row">
        <svg viewBox="0 0 16 16" aria-hidden="true"><path d="M1 6c0-2 3-3 7-3s7 1 7 3v1h-3.5V5.5h-7V7H1zm3 2h8l2 5H2zm4 1.3a1.6 1.6 0 1 0 0 3.2 1.6 1.6 0 0 0 0-3.2z"/></svg>
        (08) 9316 5172
      </p>
      <p class="contact__row">
        <svg viewBox="0 0 16 16" aria-hidden="true"><path d="M2 4h12v1L8 9 2 5zm0 2.3 6 4 6-4V12H2z"/></svg>
        info@bramblefordhomes.com.au
      </p>
      <p class="contact__address">PO Box 3817 Tarrowby WA 6987<br>47C Corvell Street, Tarrowby WA 6081</p>
    </div>
  </section>

  <section class="card card--back">
    <div class="spot-uv-art" role="img" aria-label="Spot UV gloss tree with branches and roots on charcoal"></div>
    <div class="wordmark">
      <span class="wordmark__main">Brambleford</span>
      <span class="wordmark__sub">Constructions</span>
    </div>
  </section>
</main>
</body>
</html>
```